Redesign two existing website pages and one new landing page for dental office

I need to redesign two webpages on my dental website, the Home page (http://velbridgedental.com) and the Dental Implant Services page (http://www.velbridgedental.com/dental-implant-services) and also create a landing page for the Dental Implant Services page.

Please use the same color scheme, slogans and subtitles for the redesign pages and create a reserved video spot on each page. The video spots should not be too big but not too small either and positioned in a central key location on each of the pages. The final redesigned pages should communicate leadership, confidence and trust.

The new landing page for the Dental implant Services page must not have any hyperlinks on the page and must entice the viewer to give name and email before downloading a "Free" eBook called "Is a Fuller Smile Worth the Wait?" Any added photo images to this new page must be smiling.
Updates

Project Deadline Extended Reason: I got feedback that my project was not long enough so I'm extending it by 5 days. Added Thursday, April 16, 2015

Target Market(s)

People who are middle-age to seniors.

Industry/Entity Type

Dental

Coding

Coded - Design and coding required

Number of Pages Required

3 page

Requirements
Must have
• Compatible with existing website colors and theme.

```html
<!DOCTYPE html>
<html lang="en">
<head>
<meta charset="utf-8">
<title>Velbridge Dental Care – Dental Service</title>
<link href="https://fonts.googleapis.com/css2?family=Open+Sans:wght@300;400;600&display=swap" rel="stylesheet">
<style>
:root{
  --teal:#336869;
  --teal-text:#3a6f70;
  --ink:#333;
  --rule:#b5b5b5;
  --frame:#cfcfcf;
  --white:#fff;
  --video:#1c1c1c;
}
*{margin:0;padding:0;box-sizing:border-box}
html,body{width:1200px;height:900px;overflow:hidden;background:var(--white)}
body{position:relative;font-family:"Open Sans",sans-serif;color:var(--teal-text)}
.abs{position:absolute}

.brand{left:62px;top:28px;font-size:26px;font-weight:400;color:var(--teal);letter-spacing:-0.5px;display:flex;align-items:center;gap:8px}
.brand-mark{width:10px;height:10px;border-radius:50%;background:var(--teal)}
.address{left:630px;top:48px;width:268px;text-align:right;font-size:13px;line-height:18px;color:var(--ink)}
.phone{left:940px;top:46px;font-size:30px;color:var(--teal)}
.social{left:993px;top:17px;display:flex;gap:9px}
.social .sq{width:22px;height:20px;background:#444;border-radius:3px}
.social svg{display:block}

.nav{left:2px;top:101px;width:1192px;height:61px;background:var(--teal);display:flex;align-items:center;padding-left:70px}
.nav a{color:var(--white);text-decoration:none;font-size:17px;text-transform:uppercase;margin-right:34px}
.nav a.tight{margin-right:10px}

.page-title{left:0;top:205px;width:1200px;height:60px}
.page-title .line{position:absolute;top:29px;height:8px;background:var(--rule)}
.page-title h1{position:absolute;left:448px;top:0;font-size:46px;font-weight:400;color:var(--teal)}

.service-card{left:62px;width:194px;text-align:center}
.service-card .photo{width:194px;height:194px;border-radius:50%;border:4px solid var(--frame);background:radial-gradient(circle,#f4f4f4,#d9d9d9)}
.service-card .label{margin-top:12px;font-size:20px;font-weight:600;color:var(--teal)}

.action{top:305px;width:255px;height:62px;background:var(--teal);color:var(--white);font-size:17px;line-height:21px;display:flex;align-items:center}
.action .icon{width:46px;height:68px;margin-top:-6px;margin-right:20px;flex:none}

.section-title{left:327px;top:414px;font-size:28px;font-weight:600;color:var(--teal)}
.copy{left:327px;top:475px;width:545px;font-size:16.5px;line-height:21px;color:var(--teal-text)}
.copy p{margin-bottom:21px}
.portrait{left:903px;top:458px;width:213px;height:245px;border:6px solid var(--frame);border-radius:4px;background:linear-gradient(160deg,#f3efec,#d8cfc8)}

.divider{left:331px;top:745px;width:810px;height:1px;background:var(--teal)}
.learn{left:323px;top:798px;font-size:70px;font-weight:300;line-height:80px;color:var(--teal)}
.video{left:563px;top:780px;width:578px;height:130px;background:radial-gradient(ellipse at 50% 100%,#3a3a3a,var(--video))}
.video svg{position:absolute;left:240px;top:104px}
</style>
</head>
<body>

<header>
  <div class="abs brand"><span class="brand-mark"></span>Velbridge Dental Care</div>
  <div class="abs social" aria-label="Contact and social links">
    <svg width="24" height="20" viewBox="0 0 24 20"><rect x="1" y="3" width="22" height="15" rx="2" fill="#444"/><path d="M1 4 L12 12 L23 4" stroke="#fff" stroke-width="2" fill="none"/></svg>
    <span class="sq"></span><span class="sq"></span><span class="sq"></span><span class="sq"></span>
  </div>
  <div class="abs address">Harborview Medical Plaza, 2480<br>Linden Road, Ste. #310, Fairhaven, TX 77590</div>
  <div class="abs phone">(555) 014-2290</div>
</header>

<nav class="abs nav">
  <a href="#">Home</a><a href="#">About Us</a><a href="#">Dental Service</a><a href="#">Blog</a><a href="#" class="tight">Contact Us</a><a href="#">Testimonials</a>
</nav>

<div class="abs page-title">
  <span class="line" style="left:48px;width:366px"></span>
  <h1>Dental Service</h1>
  <span class="line" style="left:775px;width:366px"></span>
</div>

<aside>
  <div class="abs service-card" style="top:295px">
    <div class="photo" role="img" aria-label="Toothbrush, toothpaste and floss"></div>
    <div class="label">Dental Hygein</div>
  </div>
  <div class="abs service-card" style="top:555px">
    <div class="photo" role="img" aria-label="Dentist figure with medical kit beside a tooth"></div>
    <div class="label">Dental Emergency</div>
  </div>
  <div class="abs service-card" style="top:815px">
    <div class="photo" role="img" aria-label="Row of white teeth"></div>
  </div>
</aside>

<div class="abs action" style="left:327px">
  <svg class="icon" viewBox="0 0 46 68"><rect x="1" y="1" width="44" height="66" rx="4" fill="#9fb6b6" stroke="#336869" stroke-width="2"/><rect x="7" y="9" width="32" height="44" fill="#e4eded"/><text x="23" y="42" text-anchor="middle" font-family="Open Sans,sans-serif" font-size="26" fill="#336869">A</text><circle cx="23" cy="60" r="3" fill="#336869"/></svg>
  <span>Get Dr. Velbridge's<br>Mobile App</span>
</div>
<div class="abs action" style="left:606px">
  <svg class="icon" viewBox="0 0 46 68"><rect x="1" y="6" width="44" height="60" fill="#9fb6b6" stroke="#336869" stroke-width="2"/><rect x="1" y="6" width="44" height="10" fill="#336869"/><g fill="#e4eded"><rect x="6" y="22" width="8" height="8"/><rect x="19" y="22" width="8" height="8"/><rect x="32" y="22" width="8" height="8"/><rect x="6" y="35" width="8" height="8"/><rect x="19" y="35" width="8" height="8"/><rect x="32" y="35" width="8" height="8"/><rect x="6" y="48" width="8" height="8"/><rect x="19" y="48" width="8" height="8"/><rect x="32" y="48" width="8" height="8"/></g><rect x="10" y="1" width="4" height="9" fill="#336869"/><rect x="32" y="1" width="4" height="9" fill="#336869"/></svg>
  <span>Request an<br>Appointment</span>
</div>
<div class="abs action" style="left:885px">
  <svg class="icon" viewBox="0 0 46 68"><rect x="1" y="5" width="44" height="62" fill="#e4eded" stroke="#336869" stroke-width="2"/><rect x="15" y="1" width="16" height="8" fill="#336869"/><g stroke="#336869" stroke-width="2"><line x1="8" y1="20" x2="38" y2="20"/><line x1="8" y1="29" x2="38" y2="29"/><line x1="8" y1="38" x2="38" y2="38"/><line x1="8" y1="47" x2="38" y2="47"/><line x1="8" y1="56" x2="30" y2="56"/></g></svg>
  <span>New Patient<br>Online Forms</span>
</div>

<main>
  <h2 class="abs section-title">Dental Hygiene Services</h2>
  <div class="abs copy">
    <p>Dental Hygiene Services promote optimum dental health and are sensible for all ages. A person’s oral well-being requires a dental check-up and a professional cleaning on a regular basis.</p>
    <p>Finding dental problems early on before they become serious and are costly to treat is a compelling reason to utilize modern dental hygiene services.</p>
    <p>At Velbridge Dental Care, we are here to help you identify and reach your dental health objectives.</p>
  </div>
  <div class="abs portrait" role="img" aria-label="Smiling woman lying down resting her chin on her hands"></div>

  <div class="abs divider"></div>
  <div class="abs learn">LEARN<br>FROM</div>
  <div class="abs video" role="img" aria-label="Video player">
    <svg width="96" height="96" viewBox="0 0 96 96"><circle cx="48" cy="48" r="44" fill="none" stroke="#fff" stroke-width="4"/></svg>
  </div>
</main>

</body>
</html>
```